Residential Remodeling Contractor needs updated business card

I need a new design for my business card.
Name of the company is Ridgefell Construction. I need a card that commands presence, strength, integrity. I have been in business for 28 years. I am a Residential Remodeling Contractor that covers all aspects of a residential remodel and build.

```html
<!DOCTYPE html>
<html lang="en">
<head>
<meta charset="UTF-8">
<title>Ridgefell Construction – Business Card</title>
<link href="https://fonts.googleapis.com/css2?family=Cinzel:wght@500;700&family=Poppins:wght@400;500&display=swap" rel="stylesheet">
<style>
  :root {
    --backdrop: #2b2b2d;
    --card-navy: #1f3b7c;
    --card-navy-deep: #182f66;
    --ink-white: #ffffff;
    --rule-soft: rgba(255,255,255,0.45);
  }
  * { margin: 0; padding: 0; box-sizing: border-box; }
  html, body { width: 1200px; height: 1108px; overflow: hidden; }
  body {
    background: var(--backdrop);
    display: flex;
    align-items: center;
    justify-content: center;
    gap: 80px;
    color: var(--ink-white);
  }
  .card {
    width: 350px;
    height: 600px;
    border-radius: 22px;
    background: var(--card-navy);
    position: relative;
    overflow: hidden;
    box-shadow: 0 18px 40px rgba(0,0,0,0.45);
  }
  .serif { font-family: "Cinzel", "Times New Roman", serif; }
  .sans { font-family: "Poppins", Arial, sans-serif; }

  /* Front */
  .brand-lockup {
    position: absolute;
    top: 110px; left: 0; right: 0;
    display: flex; align-items: center; justify-content: center; gap: 14px;
  }
  .brand-mark { width: 22px; height: 22px; background: var(--ink-white); border-radius: 50%; flex: none; }
  .brand-name {
    font-family: "Cinzel", "Times New Roman", serif;
    font-weight: 700;
    font-size: 27px;
    line-height: 1.05;
  }
  .person {
    position: absolute; top: 255px; left: 0; right: 0; text-align: center;
  }
  .person-name { font-size: 25px; font-weight: 500; letter-spacing: 1px; }
  .person-role { font-size: 13px; letter-spacing: 1.5px; margin-top: 2px; }
  .icon-row {
    position: absolute; top: 318px; left: 30px; right: 30px;
    display: flex; align-items: center; gap: 8px;
  }
  .icon-row .rule { flex: 1; height: 1px; background: var(--rule-soft); }
  .icon-tile {
    width: 26px; height: 26px; border-radius: 5px; background: var(--ink-white);
    display: flex; align-items: center; justify-content: center;
  }
  .contact {
    position: absolute; top: 362px; left: 0; right: 0; text-align: center;
    font-size: 15px; line-height: 1.55;
  }
  .contact .divider { width: 250px; height: 1px; background: var(--rule-soft); margin: 8px auto; }
  .specialty {
    position: absolute; bottom: 42px; left: 0; right: 0; text-align: center;
    font-size: 17px; font-weight: 500; line-height: 1.3;
  }

  /* Back */
  .card-back {
    background: linear-gradient(160deg, var(--card-navy) 0%, var(--card-navy) 55%, var(--card-navy-deep) 100%);
  }
  .tagline {
    position: absolute; top: 90px; left: 0; right: 0; text-align: center;
    font-size: 18px; font-weight: 500; line-height: 1.3;
  }
  .back-brand {
    position: absolute; bottom: 80px; left: 0; right: 0; text-align: center;
    font-size: 36px;
  }
</style>
</head>
<body>

  <section class="card card-front">
    <div class="brand-lockup">
      <span class="brand-mark"></span>
      <span class="brand-name">Ridgefell<br>Construction</span>
    </div>

    <div class="person">
      <p class="person-name serif">Daniel Whitmore</p>
      <p class="person-role sans">MANAGING DIRECTOR</p>
    </div>

    <div class="icon-row">
      <span class="rule"></span>
      <span class="icon-tile">
        <svg width="16" height="16" viewBox="0 0 24 24" aria-label="Phone"><path fill="#1f3b7c" d="M6.6 10.8a15 15 0 0 0 6.6 6.6l2.2-2.2c.3-.3.7-.4 1-.2 1.1.4 2.3.6 3.6.6.6 0 1 .4 1 1V20c0 .6-.4 1-1 1A17 17 0 0 1 3 4c0-.6.4-1 1-1h3.5c.6 0 1 .4 1 1 0 1.3.2 2.5.6 3.6.1.3 0 .7-.2 1z"/></svg>
      </span>
      <span class="icon-tile">
        <svg width="16" height="16" viewBox="0 0 24 24" aria-label="Email"><rect x="2" y="5" width="20" height="14" rx="1.5" fill="none" stroke="#1f3b7c" stroke-width="2"/><path d="M2 6l10 7 10-7" fill="none" stroke="#1f3b7c" stroke-width="2"/></svg>
      </span>
      <span class="icon-tile">
        <svg width="16" height="16" viewBox="0 0 24 24" aria-label="Website"><circle cx="12" cy="12" r="9" fill="none" stroke="#1f3b7c" stroke-width="2"/><path d="M3 12h18M12 3c3 3 3 15 0 18M12 3c-3 3-3 15 0 18" fill="none" stroke="#1f3b7c" stroke-width="1.6"/></svg>
      </span>
      <span class="rule"></span>
    </div>

    <div class="contact sans">
      <p>044-555 019 274</p>
      <p>info@ridgefell.com</p>
      <p>www.ridgefellbuild.com</p>
      <div class="divider"></div>
      <p>218, Harbor View Road</p>
      <p>60417, Maple County</p>
      <div class="divider"></div>
    </div>

    <p class="specialty serif">Residential Remodeling<br>Contractor</p>
  </section>

  <section class="card card-back">
    <p class="tagline sans">Built to Last,<br>Crafted with Care</p>
    <p class="back-brand brand-name">Ridgefell<br>Construction</p>
  </section>

</body>
</html>
```